glimTo.com needs a new landing page design

We need a new landing/home page design for glimto.com. glimTo is a fun and easy design tool on the web and mobile. We want to showcase not only our online web based tool, but also our mobile apps. We want a more bright, fun and vibrant look than what we currently have.

1. glimTo logo
2. menu bar
3. header text and sub header text
4. action button
5. promote both web and mobile versions
6. include pearl and vendo market pearl store download badges

Target Market(s)

20-40 year old women

Industry/Entity Type

Design

Font styles to use
Sans Serif

Requirements
Must have
• 1. glimTo logo 2. menu bar 3. header text and sub header text 4. action button 5. promote both web and mobile versions 6. include pearl and vendo market pearl store download badges
Nice to have
• Look at other software design landing pages from Drafly, Orvix, Etc.

```html
<!DOCTYPE html>
<html lang="en">
<head>
<meta charset="utf-8">
<title>glimTo — Easily Create Anything You Can Imagine</title>
<link rel="stylesheet" href="https://fonts.googleapis.com/css2?family=Jost:wght@400;500;600;700&family=Montserrat:wght@600;700;800&family=Parisienne&display=swap">
<style>
:root{
  --orange:#f7941d;
  --orange-deep:#f26a1a;
  --teal:#12a89d;
  --green:#21b573;
  --sky:#1fb0e6;
  --blue:#1a8fe0;
  --navy:#1b2a4a;
  --ink:#333a45;
  --muted:#5e6672;
  --white:#ffffff;
  --dark:#1d2633;
  --gray-bg:#ececec;
  --head:'Montserrat',sans-serif;
  --body:'Jost',sans-serif;
  --script:'Parisienne',cursive;
}
*{box-sizing:border-box;margin:0;padding:0}
html,body{width:1200px;height:4873px;overflow:hidden}
body{font-family:var(--body);color:var(--ink);background:var(--white);position:relative}
.section{position:absolute;left:0;width:1200px;overflow:hidden}
.abs{position:absolute}
.btn{position:absolute;display:flex;align-items:center;justify-content:center;gap:6px;font-family:var(--head);font-weight:700;font-size:11px;letter-spacing:.5px;color:var(--white);text-transform:uppercase}
.btn-orange{background:var(--orange)}
.btn-teal{background:var(--teal)}
.btn-outline{border:2px solid var(--white)}
.arrow-dot{width:9px;height:9px;border-radius:50%;background:var(--white);display:inline-block;position:relative}
.arrow-dot::after{content:"";position:absolute;left:3px;top:2px;border-left:4px solid var(--orange);border-top:2.5px solid transparent;border-bottom:2.5px solid transparent}
.btn-teal .arrow-dot::after{border-left-color:var(--teal)}
.script{font-family:var(--script);font-weight:400}
.logo{font-family:var(--head);font-weight:700;color:var(--white);letter-spacing:.5px}

/* hero */
.hero{top:0;height:590px}
.hero-photo{position:absolute;inset:0;background:linear-gradient(100deg,#b9c2cc 0%,#7e8c9a 45%,#3a4350 75%,#20252e 100%)}
.nav-logo{left:172px;top:14px;font-size:32px}
.nav-menu{left:460px;top:24px;display:flex;gap:30px;font-size:13px;color:var(--white)}
.nav-login,.nav-signup{top:18px;height:30px;font-size:13px;font-family:var(--body);font-weight:500;text-transform:none;letter-spacing:0}
.nav-login{left:822px;width:98px;background:var(--orange)}
.nav-signup{left:938px;width:90px;background:var(--green)}
.hero-script{left:176px;top:240px;font-size:46px;color:var(--white)}
.hero-title{left:176px;top:306px;font-family:var(--head);font-weight:800;font-size:50px;color:var(--white);letter-spacing:.5px}
.hero-cta{left:178px;top:394px;width:126px;height:40px}
.hero-arrow{top:275px;width:57px;height:100px;background:rgba(30,34,42,.85);display:flex;align-items:center;justify-content:center}

/* features */
.features{top:590px;height:517px;background:linear-gradient(160deg,var(--sky) 0%,#1aa8d8 50%,#10a29a 100%)}
.feature{position:absolute;top:87px;width:269px;text-align:center;color:var(--white)}
.feature-img{width:269px;height:189px;box-shadow:0 6px 14px rgba(0,0,0,.25)}
.feature h3{font-family:var(--head);font-size:13px;font-weight:700;margin-top:24px;letter-spacing:.3px}
.feature p{font-size:12px;line-height:1.6;margin:12px 6px 0}
.feature .btn{position:relative;margin:20px auto 0;width:100px;height:30px}

/* anything */
.anything{top:1107px;height:520px}
.tool-panel{left:163px;top:-19px;width:91px;height:161px;border-radius:6px;background:linear-gradient(180deg,#2b3038,#171a20);box-shadow:0 6px 12px rgba(0,0,0,.2)}
.center-script{width:1200px;text-align:center;color:var(--orange);font-size:30px}
.center-title{width:1200px;text-align:center;font-family:var(--head);font-weight:700;font-size:34px;color:var(--navy);letter-spacing:.5px}
.anything .sub{width:1200px;top:160px;text-align:center;font-size:13px;color:var(--muted)}
.pro-pill{display:inline-block;background:var(--sky);color:var(--white);border-radius:50%;padding:4px 3px;font-size:10px;font-weight:600}
.tool{position:absolute;top:208px;width:270px;height:240px;text-align:center}
.tool svg{display:block;margin:0 auto}
.tool h4{font-family:var(--body);font-weight:500;font-size:16px;color:var(--navy);margin-top:14px}
.tool p{font-size:12px;line-height:1.65;color:var(--muted);margin:10px 12px 0}
.tool .btns{position:absolute;top:202px;left:0;width:270px;height:30px}

/* subscription */
.subscribe{top:1627px;height:331px;background:linear-gradient(100deg,#f8ab2a 0%,var(--orange) 45%,var(--orange-deep) 100%)}
.sub-script{left:172px;top:88px;font-size:32px;color:var(--white)}
.pro-tag{left:350px;top:88px;background:var(--sky);color:var(--white);font-family:var(--head);font-size:9px;font-weight:700;padding:2px 5px}
.sub-title{left:172px;top:142px;font-family:var(--head);font-weight:700;font-size:29px;color:var(--white)}
.sub-text{left:719px;top:93px;width:310px;font-size:12.5px;line-height:1.75;color:var(--white)}
.sub-more{left:719px;top:207px;width:140px;height:34px}

/* app */
.app{top:1958px;height:690px}
.widget{left:851px;top:-18px;width:131px;height:85px;border-radius:6px;background:linear-gradient(135deg,#3b4250,#1f232b);box-shadow:0 6px 12px rgba(0,0,0,.2)}
.app-title{left:172px;top:122px;font-family:var(--head);font-weight:800;font-size:33px;color:var(--navy)}
.app-sub{left:172px;top:170px;font-size:13px;color:var(--muted)}
.app-item{position:absolute;left:172px;width:460px;height:70px}
.app-item svg{position:absolute;left:0;top:0}
.app-item h5{position:absolute;left:87px;top:10px;font-family:var(--head);font-weight:700;font-size:15px;color:var(--ink);line-height:1.3;width:360px}
.app-item p{position:absolute;left:87px;font-size:12px;color:var(--muted)}
.badge{position:absolute;top:522px;height:46px;background:#000;border-radius:6px;color:var(--white);display:flex;align-items:center;gap:10px;padding:0 12px}
.badge small{display:block;font-size:8px;letter-spacing:.5px}
.badge b{display:block;font-family:var(--body);font-weight:500;font-size:18px;line-height:1}
.badge i{width:22px;height:22px;border-radius:4px;background:var(--white);display:block}
.phone{left:690px;top:110px;width:230px;height:470px;border-radius:34px;background:linear-gradient(160deg,#3c3f47,#16181c);transform:rotate(-13deg);box-shadow:24px 30px 40px rgba(0,0,0,.22)}
.phone-screen{position:absolute;left:12px;top:12px;right:12px;bottom:12px;border-radius:24px;background:linear-gradient(180deg,#6a4a3c 0%,#3d2f2a 45%,#f2f2f2 46%,#f2f2f2 100%)}

/* why */
.why{top:2648px;height:572px;background:linear-gradient(180deg,#1b8ee2 0%,#1f9de8 100%)}
.why .center-title{top:72px;color:var(--white)}
.why-sub{width:1200px;top:123px;text-align:center;font-size:13.5px;line-height:1.75;color:var(--white)}
.monitor{left:172px;top:175px;width:401px;height:387px;background:linear-gradient(180deg,#2e3340 0%,#1a1d25 68%,#d9dde2 70%,#aab1b9 100%);border-radius:6px 6px 0 0}
.why-lead{left:611px;top:204px;font-size:13px;color:var(--white)}
.why-item{position:absolute;left:613px;width:420px;color:var(--white)}
.why-item .dot{position:absolute;left:0;top:0;width:58px;height:58px;border-radius:50%;background:radial-gradient(circle at 40% 35%,#ffc24a,var(--orange-deep))}
.why-item h6{position:absolute;left:74px;top:4px;font-family:var(--head);font-weight:700;font-size:16px}
.why-item p{position:absolute;left:74px;top:28px;font-size:12px;white-space:nowrap}
.why-cta{left:611px;top:477px;width:136px;height:32px}
.side-tools{left:1071px;top:521px;width:40px;height:183px;background:linear-gradient(180deg,#2c3039,#191c22);border-radius:3px;z-index:2}

/* meme */
.meme{top:3220px;height:503px}
.meme-art{left:132px;top:43px;width:426px;height:422px;border-radius:50%;background:radial-gradient(circle at 50% 50%,#ff63b2 0%,#e2408f 30%,#27c3c8 55%,#15a9b2 100%)}
.meme-script{left:577px;top:70px;font-size:30px;color:var(--orange)}
.meme-title{left:577px;top:112px;font-family:var(--head);font-weight:800;font-size:33px;color:var(--navy)}
.meme-text{left:577px;top:168px;width:450px;font-size:13px;line-height:1.75;color:var(--ink)}
.meme-list{left:577px;top:263px;list-style:none;font-size:16px;color:var(--ink)}
.meme-list li{display:flex;align-items:center;gap:12px;height:39px}
.meme-list li::before{content:"";width:14px;height:14px;border-radius:50%;background:var(--navy);display:block}
.meme-cta{left:579px;top:389px;width:115px;height:34px}

/* social */
.social{top:3723px;height:458px;background:var(--gray-bg)}
.social .center-script{top:64px}
.social .center-title{top:106px}
.cover{position:absolute;top:168px;width:269px;height:195px;background:var(--white);box-shadow:0 6px 14px rgba(0,0,0,.15)}
.cover-head{height:59px;display:flex;align-items:center;justify-content:center;font-family:var(--head);font-weight:700;font-size:18px;color:var(--white)}
.cover-shot{height:136px}
.carousel-btn{position:absolute;top:246px;width:38px;height:38px;border-radius:50%;background:#8a8f96;display:flex;align-items:center;justify-content:center;z-index:2}

/* stats */
.stats{top:4181px;height:276px;background:linear-gradient(120deg,var(--sky) 0%,#19a6d4 60%,var(--teal) 100%)}
.stat{position:absolute;top:81px;width:193px;height:112px;border:2px solid var(--white);display:flex;align-items:center;gap:12px;padding-left:16px;color:var(--white)}
.stat .icon{width:58px;height:50px;border-radius:10px}
.stat b{display:block;font-family:var(--head);font-size:13px;font-weight:700}
.stat span{display:block;font-size:15px;margin-top:4px}

/* cta + footer */
.footer{top:4457px;height:416px;background:var(--dark);color:var(--white)}
.cta-line{left:255px;top:44px;font-family:var(--head);font-size:29px;font-weight:500}
.cta-line strong{font-weight:800}
.cta-btn{left:816px;top:41px;width:130px;height:40px;border:2px solid var(--orange)}
.cta-btn.btn{color:var(--white)}
.foot-logo{left:172px;top:143px;font-size:38px}
.foot-about{left:172px;top:226px;width:255px;font-size:12px;line-height:1.8;color:#b9c0cb}
.foot-about a{color:var(--orange);text-decoration:none}
.foot-col h6{font-family:var(--head);font-size:12px;font-weight:700;letter-spacing:.5px;margin-bottom:14px}
.foot-col ul{list-style:none;font-size:12.5px;color:#b9c0cb;line-height:1.6}
.blog{left:543px;top:164px;width:260px}
.blog li{margin-bottom:17px}
.links{left:927px;top:164px}
.links li{margin-bottom:11px}
.copy{left:172px;top:352px;font-size:11.5px;color:#b9c0cb}
.copy span{color:var(--sky)}
</style>
</head>
<body>

<header class="section hero">
  <div class="hero-photo" role="img" aria-label="Photo of a hand holding a phone showing the glimTo app home screen with design templates"></div>
  <div class="abs logo nav-logo">glimTo</div>
  <nav class="abs nav-menu"><span>Edit</span><span>Collage</span><span>Design</span><span>Touch Up</span><span>More</span></nav>
  <a class="btn nav-login">Login</a>
  <a class="btn nav-signup">Signup</a>
  <div class="abs script hero-script">Easily Create Anything</div>
  <h1 class="abs hero-title">YOU CAN IMAGINE</h1>
  <a class="btn btn-orange hero-cta">Get Started</a>
  <div class="abs hero-arrow" style="left:0"><svg width="22" height="40" viewBox="0 0 22 40"><path d="M19 2 3 20l16 18" fill="none" stroke="#fff" stroke-width="2"/></svg></div>
  <div class="abs hero-arrow" style="right:0"><svg width="22" height="40" viewBox="0 0 22 40"><path d="M3 2l16 18L3 38" fill="none" stroke="#fff" stroke-width="2"/></svg></div>
</header>

<section class="section features">
  <div class="feature" style="left:172px">
    <div class="feature-img" role="img" aria-label="Yellow collage of portrait photos with text, borders and stickers" style="background:linear-gradient(135deg,#e9d21a,#b8a60f)"></div>
    <h3>ADD TEXT, BORDERS &amp; STICKERS</h3>
    <p>A vast array of fonts, graphics and other goodies for your photo editing pleasure.</p>
    <a class="btn btn-orange">Try it <i class="arrow-dot"></i></a>
  </div>
  <div class="feature" style="left:466px">
    <div class="feature-img" role="img" aria-label="Black and white portrait with artistic brush edit" style="background:linear-gradient(135deg,#d9d9d9,#6d6d6d)"></div>
    <h3>BASIC &amp; ADVANCED TOOLS</h3>
    <p>You don't need to be a Pixelshop expert to get up and running quickly with glimTo.</p>
    <a class="btn btn-orange">Try it <i class="arrow-dot"></i></a>
  </div>
  <div class="feature" style="left:759px">
    <div class="feature-img" role="img" aria-label="Warm filtered photo of a woman reading by the sea" style="background:linear-gradient(135deg,#f4efe6,#c79a6a)"></div>
    <h3>FAB FILTERS &amp; EFFECTS</h3>
    <p>With a single click, transform your boring photo into a masterpiece.</p>
    <a class="btn btn-orange">Try it <i class="arrow-dot"></i></a>
  </div>
</section>

<section class="section anything" style="overflow:visible">
  <div class="abs tool-panel" role="img" aria-label="Floating editor layer tool panel"></div>
  <div class="abs script center-script" style="top:48px">Easily Create</div>
  <h2 class="abs center-title" style="top:90px">ANYTHING YOU CAN IMAGINE</h2>
  <p class="abs sub">Try the FREE version or upgrade to glimTo glimTo <span class="pro-pill">PRO</span> photo editor - FREE 7 Day Trial</p>

  <div class="tool" style="left:162px">
    <svg width="70" height="66" viewBox="0 0 70 66"><rect x="6" y="6" width="42" height="36" fill="none" stroke="#222" stroke-width="2"/><path d="M10 38l12-14 9 10 6-6 9 10" fill="none" stroke="#222" stroke-width="2"/><circle cx="38" cy="16" r="4" fill="#21b573"/><path d="M46 40l14 18-5 1-3 5z" fill="#222"/></svg>
    <h4>PHOTO EDITOR</h4>
    <p>Editing photos with glimTo is simple, fun and perfect for any skill level. Everyone wins with glimTo!</p>
    <div class="btns"><a class="btn btn-orange" style="left:0;width:125px;height:30px">Try it <i class="arrow-dot"></i></a><a class="btn btn-teal" style="left:129px;width:141px;height:30px">Read more <i class="arrow-dot"></i></a></div>
  </div>
  <div class="tool" style="left:463px">
    <svg width="70" height="66" viewBox="0 0 70 66"><rect x="12" y="6" width="46" height="52" fill="none" stroke="#3a6fd8" stroke-width="2"/><rect x="17" y="11" width="17" height="20" fill="#a35bd6"/><rect x="37" y="11" width="16" height="12" fill="#21b573"/><rect x="37" y="26" width="16" height="27" fill="#f7941d"/><rect x="17" y="34" width="17" height="19" fill="#1fb0e6"/></svg>
    <h4>COLLAGE MAKER</h4>
    <p>Craft the perfect collage with glimTo's easy-to-use Collage Maker. Choose from over 1000 designs.</p>
    <div class="btns"><a class="btn btn-orange" style="left:0;width:125px;height:30px">Try it <i class="arrow-dot"></i></a><a class="btn btn-teal" style="left:129px;width:141px;height:30px">Read more <i class="arrow-dot"></i></a></div>
  </div>
  <div class="tool" style="left:765px">
    <svg width="70" height="66" viewBox="0 0 70 66"><path d="M12 10l46 46M58 10 12 56" stroke="#e2408f" stroke-width="6"/><circle cx="35" cy="33" r="8" fill="#1fb0e6"/><rect x="8" y="50" width="12" height="10" fill="#f7941d"/><rect x="50" y="6" width="12" height="10" fill="#21b573"/></svg>
    <h4>DESIGN TOOL</h4>
    <p>Be careful... Our Design Tool is utterly addictive! Make cards, flyers, or the perfect social media post.</p>
    <div class="btns"><a class="btn btn-orange" style="left:0;width:125px;height:30px">Try it <i class="arrow-dot"></i></a><a class="btn btn-teal" style="left:129px;width:141px;height:30px">Read more <i class="arrow-dot"></i></a></div>
  </div>
</section>

<section class="section subscribe">
  <div class="abs script sub-script">Try glimTo glimTo</div>
  <span class="abs pro-tag">PRO</span>
  <h2 class="abs sub-title">SUBSCRIPTION FREE FOR 7 DAYS</h2>
  <p class="abs sub-text">Get the most out of glimTo with glimTo PRO. You get loads of extra fonts, stickers, and filters. Zap all those annoying ads, and save your work at the highest quality.</p>
  <a class="btn btn-outline sub-more">Learn more <i class="arrow-dot"></i></a>
</section>

<section class="section app" style="overflow:visible">
  <div class="abs widget" role="img" aria-label="Floating colour and layout editor widget"></div>
  <h2 class="abs app-title">GET THE GLIMTO APP</h2>
  <p class="abs app-sub">Don't miss glimto on your phone or tablet!</p>

  <div class="app-item" style="top:218px">
    <svg width="64" height="70" viewBox="0 0 64 70"><path d="M32 2l28 16v34L32 68 4 52V18z" fill="#1a8fe0"/><path d="M24 46V30l7-10 3 2-2 8h10v16z" fill="#ffc24a"/></svg>
    <h5>Enjoy the same features as the website</h5><p style="top:34px">Edit photos, make collages, make memes and more.</p>
  </div>
  <div class="app-item" style="top:312px">
    <svg width="64" height="70" viewBox="0 0 64 70"><path d="M32 2l28 16v34L32 68 4 52V18z" fill="#f26a1a"/><rect x="20" y="22" width="24" height="24" fill="#ffc24a"/></svg>
    <h5>Over 10 million downloads!</h5><p style="top:34px">Check out our reviews, our users are loving his app.</p>
  </div>
  <div class="app-item" style="top:412px">
    <svg width="64" height="70" viewBox="0 0 64 70"><path d="M32 2l28 16v34L32 68 4 52V18z" fill="#12a89d"/><text x="32" y="43" text-anchor="middle" font-family="Jost,sans-serif" font-size="22" fill="#ffc24a">Aa</text></svg>
    <h5>More fonts and stickers than any other mobile app.</h5><p style="top:54px">Seriously, check it out. You won't be bored a.</p>
  </div>

  <div class="badge" style="left:172px;width:163px"><i style="border-radius:50%"></i><div><small>GET IT ON</small><b>vendo market</b></div></div>
  <div class="badge" style="left:343px;width:154px"><i></i><div><small>Available on the</small><b>pearl store</b></div></div>

  <div class="abs phone" role="img" aria-label="Phone showing the glimTo app editing an Outdoor Lifestyle design"><div class="phone-screen"></div></div>
</section>

<section class="section why" style="overflow:visible">
  <h2 class="abs center-title">WHY CHOOSE US</h2>
  <p class="abs why-sub">You don't need to be a Pixelshop expert to have fun editing your digital photos.<br>With glimTo you can start right away without ever reading a manual or taking a class.</p>
  <div class="abs monitor" role="img" aria-label="Desktop monitor showing the glimTo editor with an adopt a dog or cat poster"></div>
  <p class="abs why-lead">glimTo is free to use with no registration required!</p>
  <div class="why-item" style="top:237px"><i class="dot"></i><h6>Easy to Use</h6><p>Seriously! Become an expert the first time you use it.</p></div>
  <div class="why-item" style="top:313px"><i class="dot"></i><h6>Packed Full Of Free Content</h6><p>1000's of colorful stickers, sweet fonts, and amazing filters!</p></div>
  <div class="why-item" style="top:389px"><i class="dot" style="background:radial-gradient(circle at 40% 35%,#6fe0b0,#12a89d)"></i><h6>It Really is Fun!</h6><p>Once you start, its hard to stop... you have been warned</p></div>
  <a class="btn btn-orange why-cta">Start editing <i class="arrow-dot"></i></a>
  <div class="abs side-tools" role="img" aria-label="Vertical drawing tool palette"></div>
</section>

<section class="section meme">
  <div class="abs meme-art" role="img" aria-label="Pop art illustration of a woman with pink hair and sunglasses on a teal background"></div>
  <div class="abs script meme-script">Meme maker, cut-out tool &amp;</div>
  <h2 class="abs meme-title">DESIGN YOUR OWN EMOJI!</h2>
  <p class="abs meme-text">The fun doesn't stop with eding photos and making collages. Use glimTo to make hilarious MEME's, design custom emoji, and slice and dice photos with the Cut-Out Tool.</p>
  <ul class="abs meme-list"><li>MEME Maker &amp; MEME Stickers</li><li>Cut-Out Tool</li><li>Emoji Maker - Design your own emoji</li></ul>
  <a class="btn btn-orange meme-cta">Try it <i class="arrow-dot"></i></a>
</section>

<section class="section social">
  <div class="abs script center-script">Social media</div>
  <h2 class="abs center-title">COVER PHOTO EDITOR!</h2>
  <div class="carousel-btn" style="left:157px"><svg width="12" height="16" viewBox="0 0 12 16"><path d="M9 2 3 8l6 6" fill="none" stroke="#fff" stroke-width="2"/></svg></div>
  <div class="cover" style="left:172px"><div class="cover-head" style="background:#3b5998">Friendlo</div><div class="cover-shot" role="img" aria-label="Profile page with a bridge cover photo" style="background:linear-gradient(180deg,#cfd8e6,#7d8b78)"></div></div>
  <div class="cover" style="left:467px"><div class="cover-head" style="background:#55acee">Chirpa</div><div class="cover-shot" role="img" aria-label="Profile page with a bamboo forest cover photo" style="background:linear-gradient(180deg,#e8eef3,#4f7a3a)"></div></div>
  <div class="cover" style="left:759px"><div class="cover-head" style="background:#e52d27">Clipzone</div><div class="cover-shot" role="img" aria-label="Channel page with a city at night banner" style="background:linear-gradient(180deg,#f1f1f1,#e2408f 50%,#1d2a50)"></div></div>
  <div class="carousel-btn" style="left:1012px"><svg width="12" height="16" viewBox="0 0 12 16"><path d="M3 2l6 6-6 6" fill="none" stroke="#fff" stroke-width="2"/></svg></div>
</section>

<section class="section stats">
  <div class="stat" style="left:172px"><i class="icon" role="img" aria-label="Group of users icon" style="background:linear-gradient(135deg,#ffc24a,#f26a1a)"></i><div><b>USERS</b><span>59103696</span></div></div>
  <div class="stat" style="left:394px"><i class="icon" role="img" aria-label="Heart speech bubble icon" style="background:linear-gradient(135deg,#ff8a7a,#e5383b)"></i><div><b>LIKES</b><span>8978124</span></div></div>
  <div class="stat" style="left:615px"><i class="icon" role="img" aria-label="Download arrow icon" style="background:linear-gradient(135deg,#ff9a3c,#e4501c);border-radius:50%"></i><div><b>DOWNLOADS</b><span>10345432</span></div></div>
  <div class="stat" style="left:836px"><i class="icon" role="img" aria-label="Landscape picture icon" style="background:linear-gradient(135deg,#7fd3f7,#21b573)"></i><div><b>IMAGES</b><span>351404370</span></div></div>
</section>

<footer class="section footer">
  <p class="abs cta-line"><strong>FREE,</strong> NO REGISTRATION REQUIRED</p>
  <a class="btn cta-btn">Try it <i class="arrow-dot"></i></a>
  <div class="abs logo foot-logo">glimTo</div>
  <p class="abs foot-about">Thank you for visiting our site. Our goal is to provide a fun and easy tool that helps people be creative and express themselves. <a>Make a glimTo ›</a></p>
  <div class="abs foot-col blog"><h6>LATEST FROM BLOG</h6><ul><li>5 Easy Steps to Zombify Yourself</li><li>Halloween Party Planning Made Easy</li><li>Eat, Drink &amp; be Thankful - Free Thanksgiving Printables</li></ul></div>
  <div class="abs foot-col links"><h6>USEFUL LINKS</h6><ul><li>Help</li><li>Contact</li><li>Privacy &amp; terms</li><li>glimTo pro</li><li>Thank you</li></ul></div>
  <p class="abs copy">© 2022 <span>glimTo</span>. All right reserved</p>
</footer>

</body>
</html>
```